Quill Harbor (IT/Network Services)

Quill Harbor, LLC provides technology services to small and medium businesses. Essentially, anytime you've every thought your business might need an "IT guy" to handle something you could instead call us to handle it. Basically, you can outsource your IT needs to us.

This is a brand new company and so we'll need a brand new website. I'd like to use WordPress to handle the site since that will make things easier for me to maintain in the long run.

The site should include a, more-or-less, static front page with the dynamic data occurring on pages linked from a navigational area.

I have a logo already designed that I would like to see used in the design. The one with "white" in the title is the official logo, just added some other versions for your perusal.

Color queues from the logo but feel free to add other colors where applicable.

The site should feel somewhat corporate but with a "younger" slant (something a 25-35 year old would enjoy).

Pages (either to be added initially or by me after design completion):
"About" section - includes company history, business philosophy, etc.
"Services" section - service options, service approach, service specifics
"Testimonials" section - (eventually)
"News" section - (eventually) industry news, company news, events, blog
Contact Links

Websites to view:
The two largest local competitors:
http://www.brightmarsh-tech.example/
http://www.kelvarworks.example/
Other local competitors:
http://www.tpbllc.example/
http://www.morrowfield.example/

Other info you might find useful:
Domain: qhllc.example
Address:
417 Elm Row S
Suite 512B
Nashville, TN 37288
Phone: 615-555-0187
Emails available for use/display:
info@qhllc.example
sales@qhllc.example

Target Market(s)

Our target clients are mainly small businesses (25 or less computer users) which means we're looking at a lot of start-ups or younger companies. We'll be interacting with many entrepreneurs and young business owners.

Requirements
Must have
• Need full WP theme (not a mockup)

```html
<!DOCTYPE html>
<html lang="en">
<head>
<meta charset="utf-8">
<title>Quill Harbor – IT &amp; Network Services</title>
<link rel="stylesheet" href="https://fonts.googleapis.com/css2?family=Ubuntu:wght@500;700&family=Roboto+Condensed:wght@700&family=Arimo:wght@400;700&display=swap">
<style>
:root{
  --orange:#f58a1f;
  --orange-deep:#e3541a;
  --orange-light:#fba629;
  --blue:#1755c4;
  --blue-dark:#0f3f9a;
  --nav:#7b7f83;
  --nav-active:#6a6e72;
  --page:#e6e6e6;
  --band:#d2d3d4;
  --foot:#c6c7c8;
  --heading:#555a5e;
  --text:#4a4a4a;
  --muted:#6a6a6a;
  --white:#ffffff;
}
*{box-sizing:border-box;margin:0;padding:0}
html,body{width:840px;height:1200px;overflow:hidden}
body{background:var(--page);font-family:"Arimo",Arial,sans-serif;color:var(--text);position:relative}
.abs{position:absolute}
h2,h3{font-family:"Ubuntu",sans-serif;font-weight:700;color:var(--heading);white-space:nowrap}

/* hero */
.hero{left:0;top:0;width:840px;height:377px;background:radial-gradient(ellipse 60% 80% at 55% 60%,var(--orange-light),var(--orange) 55%,var(--orange-deep) 100%)}
.hero-photo{left:190px;top:30px;width:480px;height:347px;border-radius:200px 200px 0 0;background:linear-gradient(160deg,rgba(255,255,255,.28),rgba(240,240,240,.12) 60%,rgba(40,40,40,.18))}
.brand{left:80px;top:0;width:174px;height:133px;background:#e4e4e4;display:flex;flex-direction:column;align-items:center;justify-content:center;gap:10px}
.brand-dot{width:34px;height:34px;border-radius:50%;background:var(--orange)}
.brand-name{font-family:"Ubuntu",sans-serif;font-weight:500;font-size:19px;color:#6c6f72;letter-spacing:.5px}
.hero-title{left:424px;top:80px;width:410px;font-family:"Ubuntu",sans-serif;font-weight:700;font-size:35px;line-height:45px;color:#e9e9e9;white-space:nowrap}
.hero-cta{left:427px;top:185px;width:178px;height:39px;background:var(--blue);border:3px solid var(--white);color:var(--white);font-family:"Ubuntu",sans-serif;font-weight:700;font-size:16px;display:flex;align-items:center;justify-content:center;text-decoration:none}

/* nav */
.nav{left:0;top:377px;width:840px;height:33px;background:var(--nav);border-bottom:1px solid #9a9a9a}
.nav ul{list-style:none;display:flex;position:absolute;left:80px;top:0;height:33px;width:500px}
.nav li{font-family:"Roboto Condensed",sans-serif;font-weight:700;font-size:13px;color:var(--white);display:flex;align-items:center;justify-content:center;border-right:1px solid #8d9195;white-space:nowrap}
.nav li.current{background:var(--nav-active);color:#3c3f42}
.search{left:601px;top:6px;width:161px;height:22px;background:var(--white);display:flex}
.search span{flex:1;font-size:11px;color:#888;padding:5px 8px}
.search b{width:22px;background:var(--blue);display:flex;align-items:center;justify-content:center}

/* intro */
.intro-title{left:80px;top:448px;width:430px;font-size:19px;line-height:25px;white-space:normal}
.steps{left:80px;top:515px;width:420px;list-style:none}
.steps li{display:flex;align-items:flex-start;margin-bottom:13px;min-height:39px}
.num{flex:0 0 34px;height:34px;border-radius:50%;color:var(--white);font-family:"Ubuntu",sans-serif;font-weight:500;font-size:21px;display:flex;align-items:center;justify-content:center;margin-right:14px;margin-top:1px}
.num.one{background:#2457a8}.num.two{background:#e25a1c}.num.three{background:#5c5f62}
.steps p{font-size:10px;line-height:12.8px}
.news-title{left:540px;top:451px;font-size:17.5px}
.news{left:540px;top:482px;width:220px}
.news div{margin-bottom:12px;font-size:9.6px;line-height:12.6px}
.news a{color:var(--orange-deep);text-decoration:underline;display:block}

/* services */
.service{top:706px;width:160px}
.service-icon{width:50px;height:50px;border-radius:50%;margin-left:50px;background:radial-gradient(circle at 40% 35%,#a9c2e6,#3a5f95 70%)}
.service h3{font-size:17px;margin-top:22px}
.service p{font-size:9.2px;line-height:13.6px;margin-top:6px;color:var(--muted)}
.btn{display:inline-block;margin-top:14px;height:23px;padding:0 11px;border:1px solid #cfcfcf;background:linear-gradient(#fbfbfb,#e9e9e9);font-size:10px;font-weight:700;color:#555;line-height:21px;border-radius:2px}
.btn.primary{background:linear-gradient(#2c72d6,var(--blue-dark));color:var(--white);border-color:var(--blue-dark)}

/* band */
.band{left:0;top:976px;width:840px;height:148px;background:var(--band)}
.band h2{position:absolute;top:22px;font-size:19px}
.links{position:absolute;top:66px;list-style:none;width:112px}
.links li{font-size:8.4px;color:#555;height:20px;line-height:17px;border-bottom:1px dotted #a9a9a9;padding-left:10px;position:relative}
.links li::before{content:"";position:absolute;left:0;top:6px;border-left:4px solid #999;border-top:3px solid transparent;border-bottom:3px solid transparent}
.signup p{position:absolute;left:542px;top:54px;width:215px;font-size:8.6px;line-height:13.4px;color:#555}
.email{left:542px;top:1073px;width:140px;height:26px;background:var(--white);font-size:10px;color:#777;padding:7px 10px}
.subscribe{left:688px;top:1073px;width:72px;height:25px;background:var(--blue);color:var(--white);font-family:"Roboto Condensed",sans-serif;font-weight:700;font-size:14px;display:flex;align-items:center;justify-content:center}

/* footer */
.footer{left:0;top:1124px;width:840px;height:76px;background:var(--foot);border-top:4px solid #a9aaab}
.copy{left:80px;top:26px;font-size:8.4px;color:#555}
.foot-nav{left:80px;top:43px;font-size:8.4px;color:#555;word-spacing:2px}
.social{left:643px;top:19px;display:flex;gap:11px}
.social span{width:24px;height:23px;border-radius:4px;background:#f2f2f2;border:1px solid #b9b9b9}
</style>
</head>
<body>

<header>
  <div class="abs hero"></div>
  <div class="abs hero-photo" role="img" aria-label="Photo of a young professional in a white shirt working on a laptop"></div>
  <div class="abs brand"><span class="brand-dot"></span><span class="brand-name">Quill Harbor</span></div>
  <h1 class="abs hero-title">Does your business<br>needs an “IT Guy?”</h1>
  <a class="abs hero-cta" href="#contact">CONTACT US NOW</a>
</header>

<nav class="abs nav">
  <ul>
    <li class="current" style="width:61px">HOME</li><li style="width:87px">ABOUT US</li><li style="width:83px">SERVICES</li><li style="width:97px">TESTIMONAL</li><li style="width:72px">NEWS</li><li style="width:100px">CONTACT US</li>
  </ul>
  <div class="abs search"><span>Search...</span><b><svg width="12" height="13" viewBox="0 0 12 13"><circle cx="7" cy="5" r="3.6" fill="none" stroke="#fff" stroke-width="1.8"/><line x1="4.5" y1="7.8" x2="1.5" y2="11.5" stroke="#fff" stroke-width="2"/></svg></b></div>
</nav>

<main>
  <h2 class="abs intro-title">What we can do for you through Information Technology:</h2>
  <ol class="abs steps">
    <li><span class="num one">1</span><p>Mam libero tempore massasoluta nobis est eligendi omnis voluasassumenda est, omnis dolo- resereeledusempquibusdamet aurerum odes necessitatibus saepe eveniet utoluptates estu</p></li>
    <li><span class="num two">2</span><p>Sibero tempore massasoluta nobis est eligendi omnis voluasassumenda est, omnis dolore- sereeledusempquibusdamet aurerum odes necessitatibus saepe eveniet utoluptates estu repudiandae sintet molestiae non recusandaeltaque earum.</p></li>
    <li><span class="num three">3</span><p>Mam libero tempore massasoluta nobis est eligendi omnis voluasassumenda est, omnis dolo- resereeledusempquibusdamet aurerum odes necessitatibus saepe eveniet utoluptates estu</p></li>
  </ol>

  <h2 class="abs news-title">Quill Harbor Latest News:</h2>
  <div class="abs news">
    <div><a>20.05.2012:</a>massasoluta nobis est eligendi omnis voluasassumenda est, omnis doloreser-eeledusempquibusdamet aurerum odesom</div>
    <div><a>20.05.2012:</a>massasoluta nobis est eligendi omnis voluasassumenda est, omnis doloreser-eeledusempquibusdamet aurerum odes nece</div>
    <div><a>20.05.2012:</a>massasoluta nobis est eligendi omnis voluasassumenda est, omnis doloreser-eeledusempquibusdamet aurerum odesom</div>
  </div>

  <section class="abs service" style="left:80px">
    <div class="service-icon" role="img" aria-label="Globe network icon"></div>
    <h3>Networking</h3>
    <p>Mam libero tempore massasoluta nobis est eligendi omnis voluasas sumenda est, omnis dolseresereele dusempquibusdamet aurerum odes necessitatibus saepe eveniet uto luptates estu repudiandae sint et molestiae.</p>
    <span class="btn primary">Read More</span>
  </section>
  <section class="abs service" style="left:249px">
    <div class="service-icon" role="img" aria-label="Wrench and hammer icon" style="background:radial-gradient(circle at 40% 40%,#f3c14a,#8a8f95 70%)"></div>
    <h3>Technical Support</h3>
    <p>Mam libero tempore massasoluta nobis est eligendi omnis voluasas sumenda est, omnis dolseresereele dusempquibusdamet aurerum odes necessitatibus saepe eveniet uto luptates estu repudiandae sint et molestiae.</p>
    <span class="btn">Read More</span>
  </section>
  <section class="abs service" style="left:418px">
    <div class="service-icon" role="img" aria-label="Ruler and pencil icon" style="background:radial-gradient(circle at 40% 40%,#d9d2c4,#7a6d5f 70%)"></div>
    <h3>Project Management</h3>
    <p>Mam libero tempore massasoluta nobis est eligendi omnis voluasas sumenda est, omnis dolseresereele dusempquibusdamet aurerum odes necessitatibus saepe eveniet uto luptates estu repudiandae sint et molestiae.</p>
    <span class="btn">Read More</span>
  </section>
  <section class="abs service" style="left:607px">
    <div class="service-icon" role="img" aria-label="Globe with screwdriver icon" style="margin-left:45px;background:radial-gradient(circle at 40% 35%,#8fc0f0,#1d5cb0 70%)"></div>
    <h3>IT Solutions</h3>
    <p>Mam libero tempore massasoluta nobis est eligendi omnis voluasas sumenda est, omnis dolseresereele dusempquibusdamet aurerum odes necessitatibus saepe eveniet uto luptates estu repudiandae sint et molestiae.</p>
    <span class="btn">Read More</span>
  </section>
</main>

<section class="abs band">
  <h2 style="left:80px">IT Support and Assistance Services</h2>
  <ul class="links" style="left:80px"><li>Proactive IT Support</li><li>Business Continuity</li><li>Disaster Recover</li></ul>
  <ul class="links" style="left:228px"><li>IT Network Support</li><li>Managed IT Services</li><li>ICT Support</li></ul>
  <ul class="links" style="left:375px"><li>IT Audit</li><li>Office Relocation</li><li>IT General Support</li></ul>
  <div class="signup">
    <h2 style="left:542px">Newsletter Sign Up</h2>
    <p>Aliquam congue fermentum nisl. Mauris accumsan nulla vel diam. Sed in lacus ut enim.</p>
  </div>
</section>
<div class="abs email">Email Address:</div>
<div class="abs subscribe">Subscribe</div>

<footer class="abs footer" id="contact">
  <p class="abs copy">Quill Harbor © Copyright 2012 | Privacy Policy</p>
  <p class="abs foot-nav">Home | About Us | Services | Testimonial | News | Contact Us</p>
  <div class="abs social" aria-label="Social links"><span></span><span></span><span></span><span></span></div>
</footer>

</body>
</html>
```